Web Design for a Biotech Consulting Firm

We need a web site design for a new business based in Philadelphia called Verantel Dx. This is a consulting firm that will serve medical diagnostics industry, which is part of the life science/healthcare industry focusing on developing and marketing products that help in early detection, monitoring or management of diseases. Our consulting firm will help medical diagnostic companies to overcome key challenges in designing, evaluating and marketing new products.Our company name is Verantel Dx. Verantel is Latin word for "something" Dx represents diagnostics. The idea behind the name is that we help companies to transform the original, early product ideas ("nothing") into "something"; which is a product with full clinical utility that will help to improve health and well-being.The web site should use the visual feel of the logo (attached), be modern, simple and clean looking and represent creativity, innovation, scientific thinking and progress.
Updates

Wix Design is acceptable

Industry/Entity Type

Biotechnology

Coding

Coded - Design and coding required

Number of Pages Required

1 page

Font styles to use
Sans Serif

Requirements
Must have
• simple, clean look couple of pages
Should not have
• a lot of pages

```html
<!DOCTYPE html>
<html lang="en">
<head>
<meta charset="utf-8">
<title>Verantel Dx</title>
<link rel="stylesheet" href="https://fonts.googleapis.com/css2?family=Montserrat:wght@400;500;600;700&display=swap">
<style>
:root{
  --blue:#1a83f5;
  --blue-field:#1279f0;
  --ink:#111111;
  --text:#555555;
  --dark:#262626;
  --black:#000000;
  --card:#f4f4f4;
  --white:#ffffff;
}
*{margin:0;padding:0;box-sizing:border-box}
html,body{width:1200px;height:3156px;overflow:hidden}
body{position:relative;background:var(--white);font-family:'Montserrat',sans-serif;color:var(--text)}
.abs{position:absolute}
.accent{color:var(--blue)}

.hero-band{left:0;top:0;width:594px;height:521px;background:var(--dark)}
.brand{display:flex;align-items:center;gap:10px;font-size:20px;font-weight:500;color:var(--white)}
.brand-square{width:12px;height:12px;background:var(--blue)}
.site-brand{left:90px;top:48px}
.main-nav{top:53px;right:81px;display:flex;gap:27px;font-size:13.5px;letter-spacing:.3px}
.main-nav a{color:#555;text-decoration:none}
.main-nav a.active{color:var(--blue)}
.hero-photo{left:77px;top:125px;width:584px;height:458px;background:linear-gradient(120deg,#dfe8ee 0%,#c7d3da 40%,#eef2f4 70%,#b9c3c4 100%)}
.hero-title{right:81px;top:252px;text-align:right;font-size:38px;font-weight:700;line-height:63px;color:var(--ink)}
.hero-text{right:81px;top:397px;width:420px;text-align:right;font-size:15.5px;line-height:30px;color:#333}

.section-title{left:0;width:1200px;text-align:center;font-size:36px;font-weight:700;color:var(--ink)}
.lead{left:220px;width:760px;text-align:center;font-size:12.6px;line-height:25px;color:#666}

.service{width:323px;text-align:center}
.service-photo{width:323px;height:333px}
.service h3{margin-top:30px;font-size:20px;font-weight:500;color:#222}
.service p{margin-top:13px;font-size:12.6px;line-height:25px;color:#666;padding:0 25px}

.contact{left:0;top:1490px;width:1200px;height:531px;background:var(--blue)}
.contact .section-title{top:50px;color:var(--white)}
.contact .lead{top:110px;color:#eaf3ff}
.field{height:51px;background:var(--blue-field);color:#eaf3ff;font-size:12.6px;padding:17px 15px}
.field-message{left:77px;top:276px;width:1046px;height:103px}
.send-btn{left:495px;top:401px;width:209px;height:52px;background:var(--white);border-radius:3px;color:var(--blue);font-size:18px;font-weight:700;letter-spacing:.6px;display:flex;align-items:center;justify-content:center}

.news-title{left:80px;top:2078px;font-size:36px;font-weight:700;color:var(--ink)}
.news-lead{left:78px;top:2137px;width:690px;font-size:12.8px;line-height:25px;color:#444}
.feature-news{left:800px;top:2094px;width:323px;height:291px;background:linear-gradient(160deg,#8fa4bd 0%,#5d7290 50%,#2f3d52 100%);color:var(--white);padding:170px 18px 0}
.feature-news .date{font-size:14.5px}
.feature-news .headline{margin-top:10px;font-size:15.5px;line-height:29px}
.news-photo{width:323px;height:197px}
.news-card{width:323px;height:238px;background:var(--card);border-bottom:3px solid var(--blue);padding:32px 18px 0}
.news-card .date{font-size:14.5px;color:var(--blue)}
.news-card .headline{margin-top:16px;font-size:15.5px;line-height:29px;color:#333}
.news-card .excerpt{margin-top:12px;font-size:12.6px;line-height:25px;color:#555}

.footer{left:0;top:2782px;width:1200px;height:313px;background:var(--black)}
.subscribe{left:309px;top:2749px;width:582px;height:84px;background:var(--white);box-shadow:0 4px 18px rgba(0,0,0,.08)}
.subscribe-line{left:30px;top:62px;width:522px;height:1px;background:#ccc}
.subscribe-label{left:41px;top:38px;font-size:12.6px;color:#888}
.subscribe-icon{left:513px;top:32px}
.footer-brand{left:0;width:1200px;top:2926px;justify-content:center;font-size:21px}
.footer-nav{left:0;top:3017px;width:1200px;display:flex;justify-content:center;gap:26px;font-size:13.5px;color:var(--white)}
.copyright{left:0;top:3095px;width:1200px;height:61px;background:var(--blue);color:var(--white);font-size:12.6px;text-align:center;line-height:61px}
</style>
</head>
<body>

<div class="abs hero-band"></div>
<div class="abs brand site-brand"><span class="brand-square"></span>Verantel Dx</div>
<nav class="abs main-nav">
  <a class="active" href="#">HOME</a><a href="#">ABOUT</a><a href="#">SERVICES</a><a href="#">NEWS</a><a href="#">CONTACT</a>
</nav>
<div class="abs hero-photo" role="img" aria-label="Photo of three scientists in lab coats working at a laptop in a laboratory"></div>
<h1 class="abs hero-title">Lorem Ipsum is<br>simply <span class="accent">dummy text.</span></h1>
<p class="abs hero-text">Lorem Ipsum is simply dummy text of the printing and typesetting industry Lorem Ipsum has text.</p>

<h2 class="abs section-title" style="top:648px">Welcome to Verantel <span class="accent">Dx</span></h2>
<p class="abs lead" style="top:712px">Lorem Ipsum is simply dummy text of the printing and typesetting industry. Lorem Ipsum has been the industry's standard dummy text ever since the 1500s, when an unknown printer took a galley of type and scrambled it to make a type specimen book. It has survived not only five centuries, but also the leap into electronic typesetting.</p>
<p class="abs lead" style="top:804px">It was popularised in the 1960s with the release of Lumatype sheets containing Lorem Ipsum passages, and more recently with desktop publishing software like Pagecraft Studio including versions of Lorem Ipsum.</p>

<div class="abs service" style="left:77px;top:928px">
  <div class="service-photo" role="img" aria-label="Photo of a microscope and a hand holding a tablet" style="background:linear-gradient(135deg,#8a8580 0%,#e9d6c6 45%,#f6ede6 75%,#cfc3b8 100%)"></div>
  <h3>Development</h3>
  <p>Lorem Ipsum is simply dummy text of the printing and typesetting industry.</p>
</div>
<div class="abs service" style="left:439px;top:970px">
  <div class="service-photo" role="img" aria-label="Photo of two lab workers in caps and masks reviewing a tablet" style="background:linear-gradient(135deg,#d8dde0 0%,#eef1f3 45%,#b9cfdc 75%,#9fb6c4 100%)"></div>
  <h3>Marketing</h3>
  <p>Lorem Ipsum is simply dummy text of the printing and typesetting industry.</p>
</div>
<div class="abs service" style="left:800px;top:928px">
  <div class="service-photo" role="img" aria-label="Photo of technicians operating a control panel in a production facility" style="background:linear-gradient(135deg,#aab6c2 0%,#dfe5ea 45%,#c3ccd4 70%,#8c98a5 100%)"></div>
  <h3>Monitoring</h3>
  <p>Lorem Ipsum is simply dummy text of the printing and typesetting industry.</p>
</div>

<section class="abs contact">
  <h2 class="abs section-title">Get In Touch</h2>
  <p class="abs lead">Lorem Ipsum is simply dummy text of the printing and typesetting industry. Lorem Ipsum has been the industry's standard dummy text ever since the 1500s, when an unknown printer took a galley of type and scrambled.</p>
  <div class="abs field" style="left:77px;top:204px;width:332px">Name</div>
  <div class="abs field" style="left:434px;top:204px;width:332px">Email</div>
  <div class="abs field" style="left:789px;top:204px;width:334px">Phone</div>
  <div class="abs field field-message">Messages</div>
  <div class="abs send-btn">SEND NOW</div>
</section>

<h2 class="abs news-title">Latest <span class="accent">News</span></h2>
<p class="abs news-lead">Lorem Ipsum is simply dummy text of the printing and typesetting industry. Lorem Ipsum has been the industry's standard dummy text ever since the 1500s, when an unknown printer took a galley of type.</p>

<article class="abs feature-news" role="img" aria-label="Photo of a medical team gathered around a table, with news headline overlay">
  <div class="date">12 DEC 2018</div>
  <div class="headline">Lorem Ipsum is simply dummy text of the printing and typesetting.</div>
</article>

<div class="abs news-photo" style="left:77px;top:2227px;background:linear-gradient(135deg,#3d5f93 0%,#c9d4e0 50%,#6e86aa 100%)" role="img" aria-label="Photo of two nurses reviewing a screen"></div>
<article class="abs news-card" style="left:77px;top:2424px">
  <div class="date">12 DEC 2018</div>
  <div class="headline">Lorem Ipsum is simply dummy text of the printing and typesetting.</div>
  <div class="excerpt">Lorem Ipsum is simply dummy text of the printing and typesetting industry. Lorem Ipsum has been the industry's standard.</div>
</article>

<div class="abs news-photo" style="left:439px;top:2227px;background:linear-gradient(135deg,#4a5f6e 0%,#d6e0e6 45%,#6f8ea3 100%)" role="img" aria-label="Photo of a researcher in safety glasses pointing at a monitor"></div>
<article class="abs news-card" style="left:439px;top:2424px">
  <div class="date">12 DEC 2018</div>
  <div class="headline">Lorem Ipsum is simply dummy text of the printing and typesetting.</div>
  <div class="excerpt">Lorem Ipsum is simply dummy text of the printing and typesetting industry. Lorem Ipsum has been the industry's standard.</div>
</article>

<article class="abs news-card" style="left:800px;top:2424px">
  <div class="date">12 DEC 2018</div>
  <div class="headline">Lorem Ipsum is simply dummy text of the printing and typesetting.</div>
  <div class="excerpt">Lorem Ipsum is simply dummy text of the printing and typesetting industry. Lorem Ipsum has been the industry's standard.</div>
</article>

<footer class="abs footer"></footer>
<div class="abs subscribe">
  <div class="abs subscribe-label">Enter Your Email</div>
  <svg class="abs subscribe-icon" width="24" height="22" viewBox="0 0 24 22" aria-hidden="true">
    <path d="M23 1 L1 10 L8 12.5 L19 4.5 L10 14 L10 21 L13.5 16 L18.5 19 Z" fill="var(--blue)"/>
  </svg>
  <div class="abs subscribe-line"></div>
</div>
<div class="abs brand footer-brand"><span class="brand-square"></span>Verantel Dx</div>
<nav class="abs footer-nav">
  <span>Home</span><span>|</span><span>About</span><span>|</span><span>Services</span><span>|</span><span>News</span><span>|</span><span>Contact</span>
</nav>
<div class="abs copyright">©Verantel Dx. 2019 – All Rights Reserved.</div>

</body>
</html>
```